Business Card Design for my Real Estate Investing Company

This is for a Real Estate Investing Company that will be serving the Las Vegas Valley. Id like the following slogan included: "Building Our Neighborhood" I have attached my logo. You will see the color tones I'm interested in..in my logo. I would like the card to be double-sided with a modern, professional look.
Target Market(s)
Homeowners, banks, real estate industry
Industry/Entity Type
Real Estate
Contact Information for Business Card
name: Dale Harwick
position: Managing Member
address: 4821 Corliss Pkwy ste 207-300
Corliss Heights, NV 89184
phone: (702) 555-0143
fax: (702) 555-0187
email: SummitRidgeEstate@hollowmail.test
web: SummitRidgeEstates.test
*At the bottom of the card I would like....
We buy houses for cash....no repairs, no commissions, no fees!
Logo Text
SUMMIT RIDGE ESTATES "Investing in Our Community"
Font styles to use
Other font styles liked:
- Lora
Requirements
Must have
- On the back of the card, i'd like to have my logo large and the following statements:
- Are you considering selling your home? Want a simple, hassle-free transaction? We can help! We buy houses for cash and can close quickly! No need to do any repairs, no realtor commissions, no closing costs.....and no headaches. Let us help you with your real estate needs...!
Nice to have
- multiple colors 2 two tone on front and back

```html
<!DOCTYPE html>
<html lang="en">
<head>
<meta charset="utf-8">
<title>Summit Ridge Estates — Business Card</title>
<link href="https://fonts.googleapis.com/css2?family=Lora:ital,wght@0,400;0,500;0,600;1,400&display=swap" rel="stylesheet">
<style>
  :root {
    --backdrop: #2f2f2f;
    --brand-blue: #0d4ea6;
    --band-grey: #8d8e92;
    --card-white: #f2f2f2;
    --ink: #1c1c1c;
    --white: #ffffff;
  }
  * { margin: 0; padding: 0; box-sizing: border-box; }
  html, body { width: 1200px; height: 750px; overflow: hidden; }
  body {
    background: var(--backdrop);
    font-family: "Lora", Georgia, serif;
    position: relative;
  }
  .card {
    position: absolute;
    top: 214px;
    height: 290px;
    box-shadow: 0 2px 6px rgba(0,0,0,.45);
  }

  /* Front */
  .card-front { left: 81px; width: 505px; background: var(--card-white); color: var(--ink); }
  .top-band { position: absolute; top: 0; left: 0; right: 0; height: 18px; display: flex; }
  .top-band .band-blue { width: 321px; background: var(--brand-blue); }
  .top-band .band-gap { width: 3px; background: var(--white); }
  .top-band .band-grey { flex: 1; background: var(--band-grey); }

  .brand { position: absolute; }
  .brand-row { display: flex; align-items: center; gap: 7px; }
  .brand-mark { width: 14px; height: 14px; }
  .brand-name { font-weight: 500; white-space: nowrap; }
  .brand-slogan { font-style: italic; white-space: nowrap; }

  .card-front .brand { left: 32px; top: 56px; }
  .card-front .brand-mark { background: var(--brand-blue); }
  .card-front .brand-name { color: var(--brand-blue); font-size: 19px; letter-spacing: .3px; }
  .card-front .brand-slogan { font-size: 8.5px; letter-spacing: 2.4px; margin-top: 8px; color: var(--ink); }

  .holder-name { position: absolute; left: 31px; top: 145px; font-size: 15px; font-weight: 400; color: var(--brand-blue); }
  .holder-role { position: absolute; left: 31px; top: 163px; font-size: 13px; display: flex; align-items: center; width: 442px; }
  .holder-role::after { content: ""; flex: 1; height: 2px; background: var(--brand-blue); margin-left: 5px; margin-top: 2px; }

  .contact-list { position: absolute; left: 30px; top: 190px; list-style: none; font-size: 12.3px; line-height: 17.3px; }
  .contact-list li { display: flex; align-items: center; gap: 4px; }
  .contact-list svg { width: 11px; height: 11px; fill: var(--brand-blue); flex: none; }

  .address { position: absolute; left: 288px; top: 226px; font-size: 12.8px; line-height: 16px; font-style: normal; }
  .tagline { position: absolute; left: 31px; top: 264px; font-size: 15.2px; color: var(--brand-blue); white-space: nowrap; }

  /* Back */
  .card-back { left: 613px; width: 502px; background: var(--brand-blue); color: var(--white); text-align: center; }
  .card-back .brand { left: 0; right: 0; top: 58px; display: flex; flex-direction: column; align-items: center; }
  .card-back .brand-mark { background: var(--white); width: 20px; height: 20px; }
  .card-back .brand-name { font-size: 27px; letter-spacing: .4px; }
  .card-back .brand-slogan { font-size: 10px; letter-spacing: 3px; margin-top: 12px; }
  .pitch { position: absolute; left: 0; right: 0; top: 141px; font-size: 13.6px; line-height: 19px; }
  .pitch .help { font-size: 19px; line-height: 22px; margin-bottom: 8px; }
  .pitch .detail { font-size: 13.4px; }
</style>
</head>
<body>

<section class="card card-front" aria-label="Business card front">
  <div class="top-band"><span class="band-blue"></span><span class="band-gap"></span><span class="band-grey"></span></div>

  <div class="brand">
    <div class="brand-row"><span class="brand-mark"></span><span class="brand-name">SUMMIT RIDGE ESTATES</span></div>
    <p class="brand-slogan">"Building Our Neighborhood"</p>
  </div>

  <h1 class="holder-name">DALE HARWICK</h1>
  <p class="holder-role">Managing Member</p>

  <ul class="contact-list">
    <li><svg viewBox="0 0 12 12"><rect x="0" y="0" width="12" height="12" rx="2"/><path d="M3.4 2.4l1.6 1.7-.8 1c.5 1 1.3 1.8 2.3 2.3l1-.8 1.7 1.6-1 1.3C5.5 9.2 2.8 6.5 2.2 3.4z" fill="#f2f2f2"/></svg>(702) 555-0143</li>
    <li><svg viewBox="0 0 12 12"><rect x="3" y="0.5" width="6" height="3"/><rect x="0.5" y="4" width="11" height="5" rx="1"/><rect x="3" y="7.5" width="6" height="4" fill="#f2f2f2" stroke="#0d4ea6"/></svg>(702) 555-0187</li>
    <li><svg viewBox="0 0 12 12"><rect x="0" y="2" width="12" height="8"/><path d="M0.5 2.5L6 7l5.5-4.5" fill="none" stroke="#f2f2f2" stroke-width="1"/></svg>SummitRidgeEstate@hollowmail.test</li>
    <li><svg viewBox="0 0 12 12"><g fill="none" stroke="#0d4ea6" stroke-width="0.9"><circle cx="6" cy="6" r="5.2"/><ellipse cx="6" cy="6" rx="2.3" ry="5.2"/><path d="M1 6h10M2 3.3h8M2 8.7h8"/></g></svg>SummitRidgeEstates.test</li>
  </ul>

  <address class="address">4821 Corliss Pkwy ste 207-300<br>Corliss Heights, NV 89184</address>

  <p class="tagline">We buy houses for cash....no repairs, no commissions, no fees!</p>
</section>

<section class="card card-back" aria-label="Business card back">
  <div class="brand">
    <div class="brand-row"><span class="brand-mark"></span><span class="brand-name">SUMMIT RIDGE ESTATES</span></div>
    <p class="brand-slogan">"Building Our Neighborhood"</p>
  </div>

  <div class="pitch">
    <p>Are you considering selling your home?</p>
    <p>Want a simple, hassle-free transaction?</p>
    <p class="help">We can help!</p>
    <p class="detail">We buy houses for cash and can close quickly!</p>
    <p class="detail">No need to do any repairs, no realtor commissions, no closing costs.....</p>
    <p class="detail">and no headaches. Let us help you with your real estate needs...!</p>
  </div>
</section>

</body>
</html>
```